Resposive web site in 4 languages + image gallery + logo design

We need a web page, which will work on all devices.
I have uploaded web page concept.
Company name: Praxelun
Industry/Entity Type
It Company
Logo Text
quality matters
Coding
Coded - Design and coding required
Number of Pages Required
1 page

```html
<!DOCTYPE html>
<html lang="en">
<head>
<meta charset="utf-8">
<title>Praxelun</title>
<link href="https://fonts.googleapis.com/css2?family=Arvo:wght@400;700&family=Open+Sans:wght@400;600&display=swap" rel="stylesheet">
<style>
:root{
  --wood-dark:#3a2317;
  --wood:#5a3522;
  --accent:#8a5432;
  --accent-soft:#b98a63;
  --beige:#efe5da;
  --grey-band:#ececec;
  --text:#555;
  --text-light:#888;
  --white:#fff;
  --footer:#2b2b2b;
  --line:#ddd;
}
*{box-sizing:border-box;margin:0;padding:0}
html,body{width:1200px;height:2352px;overflow:hidden}
body{font-family:"Open Sans",Arial,sans-serif;color:var(--text);background:var(--white);font-size:13px;line-height:1.6}
.wrap{width:940px;margin:0 auto;position:relative}
h1,h2,h3,.logo{font-family:"Arvo",Georgia,serif;font-weight:400}

/* header + hero */
.hero{position:relative;height:560px;background:linear-gradient(160deg,#cfd6dc 0%,#a58a6c 35%,#7a4e2e 60%,#c9a27a 85%,#e8dccd 100%)}
.topbar{position:absolute;left:0;right:0;top:0;height:74px;background:linear-gradient(180deg,var(--wood-dark),var(--wood))}
.topbar .wrap{display:flex;align-items:center;justify-content:space-between;height:74px}
.logo{color:var(--white);font-size:40px;letter-spacing:1px}
.nav{display:flex;align-items:center;gap:26px;font-size:13px;color:#e9d9c8}
.nav a{color:inherit;text-decoration:none}
.nav .active{color:var(--white);font-weight:600}
.lang{border:1px solid #a07a60;padding:2px 10px;border-radius:2px;font-size:12px}
.social-square{width:24px;height:24px;border:1px solid #a07a60;border-radius:2px}

.estimate{height:56px;background:var(--grey-band);border-bottom:1px solid var(--line);display:flex;align-items:center;justify-content:center;gap:18px}
.estimate p{font-family:"Arvo",Georgia,serif;font-size:17px;color:#555}
.btn{display:inline-block;border:1px solid #bbb;background:var(--white);padding:4px 14px;font-size:12px;color:#555;text-transform:uppercase;letter-spacing:.5px}

/* services */
.section-title{text-align:center;font-family:"Arvo",Georgia,serif;font-size:22px;color:#666;padding:52px 0 22px}
.service{height:280px;display:flex;align-items:center}
.service.alt{background:var(--beige)}
.service .wrap{display:flex;align-items:center;gap:44px}
.photo{flex:0 0 280px;height:210px}
.service .body{flex:1}
.service h3{font-size:40px;color:var(--accent);margin-bottom:10px}
.service .body p{font-size:12px;color:var(--text-light);line-height:1.7;margin-bottom:14px}
.tags{display:flex;flex-wrap:wrap;gap:6px 20px;list-style:none;font-family:"Arvo",Georgia,serif;font-size:17px;color:#555}
.tags li{display:flex;align-items:center;gap:6px}
.tags svg{width:14px;height:14px}

/* about */
.about{height:260px;background:var(--beige);margin-top:20px;text-align:center;padding-top:20px}
.about h2{font-size:26px;color:#666}
.about p{font-size:12px;color:var(--text-light);max-width:760px;margin:8px auto}
.about .mark{font-family:"Arvo",Georgia,serif;font-size:46px;color:#cdb8a4;line-height:1.2;margin:6px 0}
.about .tagline{font-family:"Arvo",Georgia,serif;font-size:20px;color:var(--accent)}

/* contact */
.contact{padding-top:100px;height:400px}
.contact .wrap{display:flex;justify-content:space-between}
.contact h2{font-size:32px;color:#555;margin-bottom:18px}
.contact-info{display:flex;gap:22px}
.map{width:120px;height:110px;background:linear-gradient(135deg,#eee,#d8d8d8)}
.details{list-style:none;font-size:12px;color:var(--text-light)}
.details li{display:flex;align-items:center;gap:10px;height:30px}
.details svg{width:14px;height:14px}
.socials{display:flex;gap:12px;margin-top:14px;padding-left:142px}
.socials span{width:30px;height:30px;border-radius:50%;background:#555}
.socials span:first-child{background:#3b5998}
.form{width:380px;padding-top:56px}
.form .row{display:flex;gap:14px;margin-bottom:12px}
.field{flex:1;height:30px;border:1px solid #ccc;font-size:11px;color:#aaa;padding:6px 10px}
.field.msg{height:60px}
.send{display:inline-block;background:#333;color:var(--white);font-size:11px;padding:6px 16px;margin-top:4px}

.footer{position:absolute;left:0;right:0;top:2280px;height:72px;background:var(--footer);color:#999;font-size:11px}
.footer .wrap{display:flex;justify-content:space-between;align-items:center;height:72px}
.footer nav{display:flex;gap:18px}
</style>
</head>
<body>

<header class="hero" role="img" aria-label="Photo of a bright wooden-floored dining room with large windows overlooking a snowy mountain town">
  <div class="topbar">
    <div class="wrap">
      <div class="logo">Praxelun</div>
      <nav class="nav">
        <a class="active">Services</a>
        <a>About us</a>
        <a>Contact</a>
        <span class="lang">EN ▾</span>
        <span class="social-square"></span>
      </nav>
    </div>
  </div>
</header>

<div class="estimate">
  <p>Are you interested in an estimate?</p>
  <span class="btn">Get a quote</span>
</div>

<h2 class="section-title">Our Services</h2>

<section class="service">
  <div class="wrap">
    <div class="photo" role="img" aria-label="Photo of a curved wooden spiral staircase" style="background:linear-gradient(135deg,#6a3a1f,#b06a3a 55%,#d9a778)"></div>
    <div class="body">
      <h3>Woodworks</h3>
      <p>Praxelun is a joinery studio working with solid timber. Each piece is measured, cut and finished by hand in our own workshop, so furniture, doors and stairs fit the room and last for many years of daily use. We advise on wood species and finishes.</p>
      <ul class="tags">
        <li><svg viewBox="0 0 14 14"><rect width="14" height="14" fill="#8a5432"/><path d="M3 7l3 3 5-6" stroke="#fff" stroke-width="2" fill="none"/></svg>Furniture</li>
        <li><svg viewBox="0 0 14 14"><rect width="14" height="14" fill="#8a5432"/><path d="M3 7l3 3 5-6" stroke="#fff" stroke-width="2" fill="none"/></svg>Windows</li>
        <li><svg viewBox="0 0 14 14"><rect width="14" height="14" fill="#8a5432"/><path d="M3 7l3 3 5-6" stroke="#fff" stroke-width="2" fill="none"/></svg>Doors</li>
        <li><svg viewBox="0 0 14 14"><rect width="14" height="14" fill="#8a5432"/><path d="M3 7l3 3 5-6" stroke="#fff" stroke-width="2" fill="none"/></svg>Staircases</li>
        <li><svg viewBox="0 0 14 14"><rect width="14" height="14" fill="#8a5432"/><path d="M3 7l3 3 5-6" stroke="#fff" stroke-width="2" fill="none"/></svg>Woodcarving</li>
        <li><svg viewBox="0 0 14 14"><rect width="14" height="14" fill="#8a5432"/><path d="M3 7l3 3 5-6" stroke="#fff" stroke-width="2" fill="none"/></svg>Graining</li>
      </ul>
    </div>
  </div>
</section>

<section class="service alt" style="margin-top:40px">
  <div class="wrap">
    <div class="body">
      <h3>Stoneworks</h3>
      <p>Natural stone brings calm and strength to any garden or home. We lay walls, terraces and paths, build outdoor kitchens and fireplaces, and craft smokeries and fences that weather well and blend with the landscape around them for decades.</p>
      <ul class="tags">
        <li><svg viewBox="0 0 14 14"><rect width="14" height="14" fill="#8a5432"/><path d="M3 7l3 3 5-6" stroke="#fff" stroke-width="2" fill="none"/></svg>Walls</li>
        <li><svg viewBox="0 0 14 14"><rect width="14" height="14" fill="#8a5432"/><path d="M3 7l3 3 5-6" stroke="#fff" stroke-width="2" fill="none"/></svg>Terraces</li>
        <li><svg viewBox="0 0 14 14"><rect width="14" height="14" fill="#8a5432"/><path d="M3 7l3 3 5-6" stroke="#fff" stroke-width="2" fill="none"/></svg>Paths</li>
        <li><svg viewBox="0 0 14 14"><rect width="14" height="14" fill="#8a5432"/><path d="M3 7l3 3 5-6" stroke="#fff" stroke-width="2" fill="none"/></svg>Outdoor kitchens</li>
        <li><svg viewBox="0 0 14 14"><rect width="14" height="14" fill="#8a5432"/><path d="M3 7l3 3 5-6" stroke="#fff" stroke-width="2" fill="none"/></svg>Fireplaces</li>
        <li><svg viewBox="0 0 14 14"><rect width="14" height="14" fill="#8a5432"/><path d="M3 7l3 3 5-6" stroke="#fff" stroke-width="2" fill="none"/></svg>Smokeries</li>
        <li><svg viewBox="0 0 14 14"><rect width="14" height="14" fill="#8a5432"/><path d="M3 7l3 3 5-6" stroke="#fff" stroke-width="2" fill="none"/></svg>Fences</li>
      </ul>
    </div>
    <div class="photo" role="img" aria-label="Photo of a curving stone garden path between green lawns" style="background:linear-gradient(135deg,#4f7a2e,#8fb25a 50%,#c9c3b3)"></div>
  </div>
</section>

<section class="service" style="margin-top:40px">
  <div class="wrap">
    <div class="photo" role="img" aria-label="Photo of a restored red brick house front with a dark door and white windows" style="background:linear-gradient(135deg,#7a2c22,#a8483a 50%,#2d2f3a)"></div>
    <div class="body">
      <h3>Restoration</h3>
      <p>Old houses deserve careful hands. We restore historic furniture, windows, doors, staircases and floors, keeping original details where we can and renewing what is lost with matching materials and traditional methods, so the character of the building remains.</p>
      <ul class="tags">
        <li><svg viewBox="0 0 14 14"><rect width="14" height="14" fill="#8a5432"/><path d="M3 7l3 3 5-6" stroke="#fff" stroke-width="2" fill="none"/></svg>Furniture</li>
        <li><svg viewBox="0 0 14 14"><rect width="14" height="14" fill="#8a5432"/><path d="M3 7l3 3 5-6" stroke="#fff" stroke-width="2" fill="none"/></svg>Windows</li>
        <li><svg viewBox="0 0 14 14"><rect width="14" height="14" fill="#8a5432"/><path d="M3 7l3 3 5-6" stroke="#fff" stroke-width="2" fill="none"/></svg>Doors</li>
        <li><svg viewBox="0 0 14 14"><rect width="14" height="14" fill="#8a5432"/><path d="M3 7l3 3 5-6" stroke="#fff" stroke-width="2" fill="none"/></svg>Staircases</li>
        <li><svg viewBox="0 0 14 14"><rect width="14" height="14" fill="#8a5432"/><path d="M3 7l3 3 5-6" stroke="#fff" stroke-width="2" fill="none"/></svg>Floors</li>
        <li><svg viewBox="0 0 14 14"><rect width="14" height="14" fill="#8a5432"/><path d="M3 7l3 3 5-6" stroke="#fff" stroke-width="2" fill="none"/></svg>Special Projects</li>
      </ul>
    </div>
  </div>
</section>

<section class="about">
  <h2>About Us</h2>
  <p>Praxelun is a company whose business operations include making wooden products, restoration and building structures from natural stone.</p>
  <div class="mark">Praxelun</div>
  <p>All of our products are made by craftsmen with long experience and knowledge of their fields. Our projects are always hand made, and we take requests and ideas of each client into account to achieve the best possible quality.</p>
  <div class="tagline">Quality matters</div>
</section>

<section class="contact">
  <div class="wrap">
    <div>
      <h2>Contact Info</h2>
      <div class="contact-info">
        <div class="map" role="img" aria-label="Street map showing the workshop location"></div>
        <ul class="details">
          <li><svg viewBox="0 0 14 14"><path d="M7 1a4 4 0 0 0-4 4c0 3 4 8 4 8s4-5 4-8a4 4 0 0 0-4-4z" fill="#999"/><circle cx="7" cy="5" r="1.5" fill="#fff"/></svg>Rannatee 14, 10132 Lindmaa</li>
          <li><svg viewBox="0 0 14 14"><path d="M3 1h2l1 3-1.5 1a7 7 0 0 0 4.5 4.5L10 8l3 1v2a2 2 0 0 1-2 2A10 10 0 0 1 1 3a2 2 0 0 1 2-2z" fill="#999"/></svg>+372 55 48 200</li>
          <li><svg viewBox="0 0 14 14"><rect x="1" y="3" width="12" height="8" fill="#999"/><path d="M1 3l6 5 6-5" stroke="#fff" fill="none"/></svg>info@praxelun.ee</li>
        </ul>
      </div>
      <div class="socials"><span></span><span></span><span></span><span></span></div>
    </div>
    <form class="form">
      <div class="row"><div class="field">Name</div><div class="field">Email</div></div>
      <div class="row"><div class="field msg">Message</div></div>
      <span class="send">Send</span>
    </form>
  </div>
</section>

<footer class="footer">
  <div class="wrap">
    <nav><span>Services</span><span>About us</span><span>Contact</span></nav>
    <span>© 2024 Praxelun · All rights reserved</span>
  </div>
</footer>

</body>
</html>
```